I am looking for a modern, clean and neat design for a reflexology and well being business. The business name is Gralo Tund (this is an old Latin word for wellbeing). The colours I would like are purple, white and grey. I am open to suggestions for pictures such as healing or working hands, a pair of feet, images that represent my business that you may think of....... or maybe you think no images at all would be best? My tag line is: "Relax, Renew, Revive" or "Find you balance......... Relax, Renew, Revive" I can decide which I want so I would like to see what both would look like. I would like space on the back to write the client's appointment date and time (more than once)

```html
<!DOCTYPE html>
<html lang="en">
<head>
<meta charset="utf-8">
<title>Gralo Tund – Business Card</title>
<link rel="stylesheet" href="https://fonts.googleapis.com/css2?family=Open+Sans:wght@400;600;700&display=swap">
<style>
  :root {
    --purple: #8a1fb0;
    --grey: #3f3f42;
    --grey-soft: #5a5a5e;
    --rule: #777777;
    --card: #ffffff;
    --backdrop: #e9e8ec;
  }
  * { margin: 0; padding: 0; box-sizing: border-box; }
  html, body { width: 1200px; height: 844px; overflow: hidden; }
  body {
    background: var(--backdrop);
    font-family: "Open Sans", Arial, sans-serif;
    color: var(--grey);
    position: relative;
  }
  .card {
    position: absolute;
    top: 272px;
    width: 520px;
    height: 300px;
    background: var(--card);
    box-shadow: 0 6px 20px rgba(0,0,0,.12);
  }
  .card--front { left: 60px; }
  .card--back { left: 620px; }

  .brand {
    position: absolute;
    display: flex;
    align-items: center;
    gap: 10px;
    font-size: 36px;
    font-weight: 400;
    color: var(--grey);
    letter-spacing: .5px;
    white-space: nowrap;
    line-height: 1.2;
  }
  .brand__dot {
    width: 16px; height: 16px;
    border-radius: 50%;
    background: var(--purple);
  }
  .card--front .brand { right: 36px; top: 40px; }
  .card--back .brand { right: 34px; top: 20px; font-size: 32px; }

  .tagline {
    position: absolute;
    right: 36px;
    top: 90px;
    font-size: 14px;
    font-weight: 600;
    color: var(--purple);
    letter-spacing: .4px;
    white-space: nowrap;
  }

  .contact { position: absolute; left: 36px; bottom: 24px; font-size: 14px; line-height: 1.35; }
  .contact__name { font-size: 19px; font-weight: 700; }
  .contact__name .accent { color: var(--purple); }
  .contact__role { font-size: 14px; margin-bottom: 14px; }
  .contact__address { margin-bottom: 12px; }
  .label { color: var(--purple); }
  .link { color: var(--purple); }
  .contact__row span + span { margin-left: 8px; }

  .appointment { position: absolute; left: 36px; right: 34px; top: 80px; font-size: 15px; }
  .appointment__title { font-size: 17px; font-weight: 600; color: var(--grey-soft); margin-bottom: 16px; display: flex; align-items: flex-end; }
  .appointment__title .accent { color: var(--purple); margin-left: 6px; }
  .appointment__title .dots { flex: 1; margin-left: 6px; border-bottom: 2px dotted var(--rule); height: 0; margin-bottom: 6px; }
  .field-row { display: flex; align-items: flex-end; margin-bottom: 16px; color: var(--purple); font-weight: 600; font-size: 14px; white-space: nowrap; }
  .field-row .dots { flex: 1; border-bottom: 2px dotted var(--rule); margin: 0 6px 5px; }
  .field-row .dots--short { flex: 0 0 120px; }
  .field-row .suffix { font-weight: 400; font-size: 12px; }
  .appointment__note { font-size: 13px; font-weight: 600; color: var(--grey-soft); margin-top: 2px; }
  .appointment__note .accent { color: var(--purple); }
</style>
</head>
<body>
  <section class="card card--front" aria-label="Business card front">
    <div class="brand"><span class="brand__dot"></span>Gralo Tund</div>
    <p class="tagline">Relax, Renew, Revive</p>
    <div class="contact">
      <p class="contact__name">Elin <span class="accent">Marsh</span></p>
      <p class="contact__role">Managing Director</p>
      <p class="contact__address">1234, Address GoesHere, Country, 12345</p>
      <p class="contact__row"><span><span class="label">T:</span>(044) 123 456 789</span><span><span class="label">F:</span>(044) 123456789</span><span><span class="label">M:</span>(044)123456789</span></p>
      <p class="contact__row"><span><span class="label">E:</span>info@youremail.com</span><span class="link">www.yourweb.com</span></p>
    </div>
  </section>

  <section class="card card--back" aria-label="Appointment card back">
    <div class="brand"><span class="brand__dot"></span>Gralo Tund</div>
    <div class="appointment">
      <p class="appointment__title">Your Next <span class="accent">Appointments</span><span class="dots"></span></p>
      <div class="field-row">Name :<span class="dots"></span></div>
      <div class="field-row">Date :<span class="dots"></span>Time :<span class="dots dots--short"></span><span class="suffix">AM / PM</span></div>
      <div class="field-row">Date :<span class="dots"></span>Time :<span class="dots dots--short"></span><span class="suffix">AM / PM</span></div>
      <div class="field-row">Date :<span class="dots"></span>Time :<span class="dots dots--short"></span><span class="suffix">AM / PM</span></div>
      <p class="appointment__note">If unable to keep appointment, <span class="accent">kindly give 24hrs notice.</span></p>
    </div>
  </section>
</body>
</html>
```